Garlic Farm for Farm Sales/Restaurant sales

Need a professional, but appealing to agriculture world. We are selling 27 kinds of Organic Garlic from a farm in Simla,CO. I have uploaded logo and business information-we are going to need a template, because I will need to use it for four separate people.
-We are trying to appeal to Farm to table restaurants
-As well as growers/farmers

Target Market(s)

Agriculture Sales/Restaurants-Organic

Industry/Entity Type

Agriculture

Contact Information for Business Card

Want it to look more unique then your average kelto stock card- I want it to look amazing

Font styles to use
Sans Serif

Colors
0455a3
ec1f27
fbed22
ffffff

Requirements
Must have
• Just be creative
Nice to have
• Colorful
Should not have
• plain

```html
<!DOCTYPE html>
<html lang="en">
<head>
<meta charset="utf-8">
<title>Prairie Peak Garlic – Business Card</title>
<link rel="stylesheet" href="https://fonts.googleapis.com/css2?family=Open+Sans:wght@400;600;700&display=swap">
<style>
  :root {
    --brand-red: #c21f2f;
    --brand-navy: #1d2f63;
    --paper: #ffffff;
    --backdrop: #e9e9ec;
    --text-font: "Open Sans", Arial, sans-serif;
  }
  * { box-sizing: border-box; margin: 0; padding: 0; }
  html, body { width: 1200px; height: 880px; overflow: hidden; }
  body { background: var(--backdrop); font-family: var(--text-font); position: relative; }

  .card {
    position: absolute;
    left: 320px;
    width: 560px;
    height: 320px;
    border-radius: 4px;
    box-shadow: 0 6px 18px rgba(0,0,0,0.18);
    overflow: hidden;
  }
  .card--front { top: 90px; background: var(--brand-red); }
  .card--back { top: 470px; background: var(--paper); }

  /* Front */
  .front-brand {
    position: absolute; inset: 0;
    display: flex; flex-direction: column; align-items: center; justify-content: center;
    color: var(--paper);
  }
  .front-brand__name { font-size: 40px; font-weight: 700; letter-spacing: 0.5px; }
  .front-brand__tagline { font-size: 16px; font-weight: 400; letter-spacing: 2px; margin-top: 2px; }

  /* Back */
  .back-waves { position: absolute; inset: 0; width: 560px; height: 320px; }
  .edge-mark {
    position: absolute; left: 0; top: 100px;
    width: 10px; height: 14px; background: var(--brand-red);
  }
  .contact { position: absolute; left: 42px; top: 92px; color: var(--brand-navy); }
  .contact__name { font-size: 18px; font-weight: 700; letter-spacing: 1px; text-transform: uppercase; }
  .contact__address { margin-top: 30px; font-size: 13px; line-height: 17px; }
  .contact__list { list-style: none; margin-top: 16px; font-size: 13px; }
  .contact__item { display: flex; align-items: center; gap: 8px; line-height: 20px; }
  .contact__icon {
    width: 16px; height: 16px; background: var(--brand-red);
    display: flex; align-items: center; justify-content: center;
  }

  .back-logo {
    position: absolute; right: 34px; top: 36px;
    display: flex; align-items: center; gap: 12px; color: var(--brand-navy);
  }
  .back-logo__dot { width: 52px; height: 52px; border-radius: 50%; background: var(--brand-red); flex: none; }
  .back-logo__text { display: flex; flex-direction: column; }
  .back-logo__name { font-size: 26px; font-weight: 700; line-height: 30px; }
  .back-logo__tagline { font-size: 12px; letter-spacing: 2px; color: var(--brand-red); }

  .web-address {
    position: absolute; right: 26px; bottom: 64px;
    color: var(--paper); font-size: 13px; font-weight: 600;
    transform: rotate(-22deg); transform-origin: right bottom;
  }
</style>
</head>
<body>

  <section class="card card--front" aria-label="Card front">
    <div class="front-brand">
      <span class="front-brand__name">Prairie Peak</span>
      <span class="front-brand__tagline">gourmet garlic</span>
    </div>
  </section>

  <section class="card card--back" aria-label="Card back">
    <svg class="back-waves" viewBox="0 0 560 320" aria-hidden="true">
      <path d="M0,245 C160,275 360,240 560,118 L560,126 C370,252 170,292 0,275 Z" fill="var(--brand-navy)"/>
      <path d="M0,292 C170,302 370,260 560,136 L560,320 L0,320 Z" fill="var(--brand-red)"/>
    </svg>

    <span class="edge-mark"></span>

    <div class="contact">
      <p class="contact__name">Dana Wells</p>
      <p class="contact__address">P.O. Box 12 Ridgeton,<br>CO 80000</p>
      <ul class="contact__list">
        <li class="contact__item">
          <span class="contact__icon">
            <svg width="10" height="10" viewBox="0 0 10 10" aria-hidden="true"><path d="M2,1 L4,1 L4.6,3 L3.5,3.8 C4,5 5,6 6.2,6.5 L7,5.4 L9,6 L9,8 C5,8.6 1.4,5 2,1 Z" fill="#fff"/></svg>
          </span>
          555-014-2290
        </li>
        <li class="contact__item">
          <span class="contact__icon">
            <svg width="10" height="8" viewBox="0 0 10 8" aria-hidden="true"><rect x="0.5" y="0.5" width="9" height="7" fill="none" stroke="#fff"/><path d="M0.5,0.5 L5,4.5 L9.5,0.5" fill="none" stroke="#fff"/></svg>
          </span>
          Dana@PPGarlic.com
        </li>
      </ul>
    </div>

    <div class="back-logo">
      <span class="back-logo__dot"></span>
      <span class="back-logo__text">
        <span class="back-logo__name">Prairie Peak</span>
        <span class="back-logo__tagline">gourmet garlic</span>
      </span>
    </div>

    <span class="web-address">PPGarlic.com</span>
  </section>

</body>
</html>
```